Modern & Simple Essential Oils Label

Company Name: Meadowlark Essentials

What we sell: Aromatherapy products, pure therapeutic essential oils.

Design need:
We are looking for a creative and youthful design for the labels used on small essentials oils.

I have two sizes of bottles that I use for essential oils a 5ml bottle and a 15ml bottle. They are dark Amber color glass with black lids. I like the clear labels or mayble a dark brown background. With white or clear lettering with punch of color too! Each oil type is represented by different color. (lavender- purple, lemon - yellow). The label will be the same for all the oils in the two sizes with only a different oil name & coordinating color.
5ml label size should be: 1 " x 2.625"
15ml label size should be: 1.5" x 3.5"

I have some labels that I have had another designer start on, but they aren't quite what I want and missing that something (alot!).. I don't know what. Interest maybe? Lack of design? I dunno.. they are attached. Maybe it's the logo? I don't know! But its gotta change! When I cut out a proof and put a sample on the bottle as I look straight on at the label all I see is a big dot, no logo.. nothing interesting.
Updates

Project Deadline Extended
Reason: Hi! Id like to extend this deadline. Ive been unavailable for a few days due to an illness and Im so far behind! Im feeling MUCH better and looking forward to getting caught up and move with the project. Im not sure how this works, but I attached a list of the oils that we currently have available. And in the list is the idea for the color schemes for the oils. The basic idea is for it to have a wide array of colors, so using different shades of greens, yellows, oranges and so on. So that its like a rainbow. We are not set of that particular color for that particular oil. It was just a idea list of possible colors for oils. Thanks so much!

Target Market(s)

Metro & Modern people. Interested in healthy organic living, Mostly women (some men) 20-45 who are interested in holistic healing.

Industry/Entity Type

It Company

Requirements
Must have
• A reputable look. Clean, organic, crisp, zen or spa-like feel. Modern, youthful appealing label design. Approachable and interesting, not intimidating so that I don't turn away people who are new or not familiar with how to use essential oils.
Should not have
• do NOT want the look to be anywhere close to medicinal, witchy, crafty, hippie, mystical, overly earthy, magical, or voodoo. Do not want it to look like something out of a grandmothers medicine cabinet.

```html
<!DOCTYPE html>
<html lang="en">
<head>
<meta charset="utf-8">
<title>Meadowlark Essentials – Rosemary Label</title>
<link href="https://fonts.googleapis.com/css2?family=Yellowtail&family=Questrial&family=Roboto:wght@700&display=swap" rel="stylesheet">
<style>
  :root {
    --backdrop: #e6e6e6;
    --paper: #f2f1ef;
    --paper-tint: #e9e7e4;
    --oil-red: #d9333b;
    --ink-grey: #8a8a8a;
    --white: #ffffff;
  }
  * { margin: 0; padding: 0; box-sizing: border-box; }
  html, body {
    width: 1200px;
    height: 834px;
    overflow: hidden;
    background: radial-gradient(circle at 50% 50%, #f7f7f7 0%, var(--backdrop) 75%);
  }
  .label {
    position: absolute;
    left: 180px;
    top: 237px;
    width: 840px;
    height: 360px;
    background: var(--paper);
    box-shadow: 0 2px 10px rgba(0,0,0,0.12);
    overflow: hidden;
  }
  .label__pattern {
    position: absolute;
    inset: 0 0 108px 0;
    background: linear-gradient(180deg, var(--paper) 0%, var(--paper-tint) 100%);
  }
  .oil-name {
    position: absolute;
    left: 44px;
    top: 24px;
    font-family: "Yellowtail", cursive;
    font-weight: 400;
    color: var(--oil-red);
    font-size: 118px;
    line-height: 0.82;
    transform: rotate(-6deg);
    transform-origin: left top;
  }
  .oil-name span { display: block; }
  .oil-name .line-two { margin-left: 10px; }
  .oil-facts {
    position: absolute;
    left: 500px;
    top: 44px;
    font-family: "Roboto", sans-serif;
    font-weight: 700;
    font-size: 26px;
    line-height: 1.28;
    color: var(--ink-grey);
    letter-spacing: 0.5px;
    text-transform: uppercase;
  }
  .brand-band {
    position: absolute;
    left: 0;
    right: 0;
    bottom: 38px;
    height: 70px;
    background: var(--oil-red);
    display: flex;
    align-items: center;
    justify-content: space-between;
    padding: 0 40px 0 6px;
  }
  .volume {
    font-family: "Roboto", sans-serif;
    font-weight: 700;
    font-size: 22px;
    line-height: 1;
    color: var(--white);
    writing-mode: vertical-rl;
    transform: rotate(180deg);
    white-space: nowrap;
  }
  .brand-name {
    font-family: "Questrial", sans-serif;
    font-size: 34px;
    color: var(--white);
    letter-spacing: 0.5px;
  }
</style>
</head>
<body>
  <section class="label">
    <div class="label__pattern" role="img" aria-label="Soft repeating floral pattern on textured white paper"></div>
    <h1 class="oil-name"><span class="line-one">Rose</span><span class="line-two">mary</span></h1>
    <p class="oil-facts">Rosmarinus<br>Officinalis<br>100% Pure<br>Essential Oil</p>
    <div class="brand-band">
      <span class="volume">15 ml</span>
      <span class="brand-name">Meadowlark Essentials</span>
    </div>
  </section>
</body>
</html>
```